The Lantern and the Orchard: Notes From Quiet Mornings

We need a book cover/spine and back cover for a multi author book called the Lantern and The Orchard: Notes from Quiet Mornings. This will be a collection of stories from women who major transformational stories to tell. They embark on a voyage, find themselves in uncharted territory, find friends or allies and in the end find themselves back home to themselves. I want this book cover to feel fun of wonder, adventure, intrigue with a a dainty energy. I have uploaded some images for inspiration but not to use in the design because they are not images I have permission to use.

```html
<!DOCTYPE html>
<html lang="en">
<head>
<meta charset="utf-8">
<title>The Lantern and the Orchard: Notes From Quiet Mornings</title>
<link rel="stylesheet" href="https://fonts.googleapis.com/css2?family=Cinzel:wght@400;600&display=swap">
<style>
  :root {
    --navy: #1f3c5e;
    --ink: #1d3a5c;
    --paper: #ffffff;
    --mist: #eef3f6;
    --lake: #2f6478;
    --pine: #1c3f4c;
    --sky: #dfe9ef;
    --silver: #b5bcc3;
  }
  html, body {
    margin: 0;
    padding: 0;
    width: 800px;
    height: 1200px;
    overflow: hidden;
    background: var(--paper);
  }
  .cover {
    position: relative;
    width: 800px;
    height: 1200px;
    overflow: hidden;
    background: var(--navy);
    font-family: "Cinzel", "Times New Roman", serif;
  }
  .cover-art {
    position: absolute;
    left: 0;
    top: 0;
    width: 800px;
    height: 763px;
    background:
      radial-gradient(ellipse 230px 520px at 400px 430px, var(--paper) 0%, var(--mist) 55%, rgba(238,243,246,0) 100%),
      linear-gradient(to bottom, var(--sky) 0%, var(--pine) 30%, var(--lake) 55%, #4f8596 72%, var(--mist) 92%, var(--paper) 100%);
  }
  .title {
    position: absolute;
    left: 0;
    width: 800px;
    margin: 0;
    text-align: center;
    font-weight: 400;
    font-size: 82px;
    line-height: 1;
    letter-spacing: -1px;
    white-space: nowrap;
  }
  .title-line-one {
    top: 697px;
    color: var(--ink);
  }
  .title-line-two {
    top: 776px;
    color: var(--paper);
  }
  .subtitle {
    position: absolute;
    top: 872px;
    left: 0;
    width: 800px;
    margin: 0;
    text-align: center;
    font-size: 36px;
    font-weight: 400;
    line-height: 1;
    letter-spacing: 1px;
    color: var(--silver);
    white-space: nowrap;
  }
  .author {
    position: absolute;
    top: 1100px;
    left: 0;
    width: 800px;
    margin: 0;
    text-align: center;
    font-size: 28px;
    font-weight: 600;
    line-height: 1;
    letter-spacing: 1px;
    color: var(--paper);
  }
</style>
</head>
<body>
  <main class="cover">
    <div class="cover-art" role="img" aria-label="Double-exposure artwork: a pale portrait silhouette blended with a misty mountain lake under a soft morning sky"></div>
    <h1 class="title-block">
      <span class="title title-line-one">THE LANTERN &amp;</span>
      <span class="title title-line-two">THE ORCHARD</span>
    </h1>
    <p class="subtitle">Notes From Quiet Mornings</p>
    <p class="author">Author Name</p>
  </main>
</body>
</html>
```